Business Card Design

Business Card for professional consulting firm working with large financial institutions.

Target Market(s)

Executive buyers

Industry/Entity Type

Banking

Contact Information for Business Card

Mild creativity wanted. Not boring, but do elaborate artwork.

Font styles to use
Serif
Sans Serif

Colors

Designer to choose colors to be used in the design.

Requirements
Must have
• Standard business card features - company name, individual name, telephone, website, email, locations.
Nice to have
• Two colors
Should not have
• too many colors, fancy printing, cartoons.

```html
<!DOCTYPE html>
<html lang="en">
<head>
<meta charset="utf-8">
<title>Northvale Business Card</title>
<link rel="stylesheet" href="https://fonts.googleapis.com/css2?family=Arvo:wght@400;700&family=Roboto:wght@400&display=swap">
<style>
  :root {
    --backdrop: #e2e2e2;
    --card-light: #f4f4f4;
    --card-dark: #1b1c1d;
    --ink: #111111;
    --ink-soft: #555555;
    --ink-muted: #a3a3a3;
    --logo-light: #3a3a3a;
    --logo-dark: #ffffff;
  }
  * { margin: 0; padding: 0; box-sizing: border-box; }
  html, body {
    width: 1200px;
    height: 960px;
    overflow: hidden;
    background: var(--backdrop);
  }
  .canvas {
    position: relative;
    width: 1200px;
    height: 960px;
  }
  .card {
    position: absolute;
    box-shadow: 0 2px 4px rgba(0,0,0,0.35);
  }
  .card-front {
    left: 314px; top: 113px;
    width: 601px; height: 343px;
    background: var(--card-light);
  }
  .card-back {
    left: 311px; top: 472px;
    width: 599px; height: 342px;
    background: var(--card-dark);
    display: flex;
    align-items: center;
    justify-content: center;
  }
  .brand {
    font-family: 'Arvo', serif;
    font-weight: 400;
    letter-spacing: 0.5px;
  }
  .card-front .brand {
    position: absolute;
    right: 70px; top: 62px;
    font-size: 28px;
    color: var(--logo-light);
  }
  .card-back .brand {
    font-size: 34px;
    color: var(--logo-dark);
  }
  .holder {
    position: absolute;
    left: 43px; top: 147px;
  }
  .holder-name {
    font-family: 'Arvo', serif;
    font-weight: 700;
    font-size: 21px;
    color: var(--ink);
    letter-spacing: 0.3px;
    line-height: 26px;
  }
  .holder-role {
    font-family: 'Arvo', serif;
    font-size: 13px;
    color: var(--ink-muted);
    line-height: 17px;
  }
  .address {
    margin-top: 13px;
    font-family: 'Roboto', sans-serif;
    font-size: 14px;
    line-height: 19px;
    color: var(--ink-soft);
  }
  .contact-list {
    list-style: none;
    margin-top: 11px;
    font-family: 'Roboto', sans-serif;
    font-size: 14px;
    line-height: 19.5px;
    color: var(--ink-soft);
  }
  .contact-list li {
    display: flex;
    align-items: center;
    gap: 7px;
  }
  .contact-icon {
    width: 13px; height: 13px;
    fill: var(--ink);
    flex: none;
  }
</style>
</head>
<body>
<main class="canvas">
  <section class="card card-front">
    <div class="brand">northvale</div>
    <div class="holder">
      <h1 class="holder-name">DANIEL HARLOW</h1>
      <p class="holder-role">CEO/FOUNDER</p>
      <p class="address">4120 Willow Court<br>Juneau, Alaska 99801</p>
      <ul class="contact-list">
        <li>
          <svg class="contact-icon" viewBox="0 0 24 24" aria-hidden="true"><path d="M6.6 10.8a15.1 15.1 0 0 0 6.6 6.6l2.2-2.2a1 1 0 0 1 1-.25 11.4 11.4 0 0 0 3.6.57 1 1 0 0 1 1 1V20a1 1 0 0 1-1 1A17 17 0 0 1 3 4a1 1 0 0 1 1-1h3.5a1 1 0 0 1 1 1c0 1.25.2 2.45.57 3.57a1 1 0 0 1-.25 1z"/></svg>
          555 210 4873
        </li>
        <li>
          <svg class="contact-icon" viewBox="0 0 24 24" aria-hidden="true"><path d="M2 5h20v14H2z M3.5 6.5 12 12.5l8.5-6" fill="none" stroke="#111" stroke-width="0"/><path d="M2 5h20v2l-10 6L2 7z"/><path d="M2 9l10 6 10-6v10H2z"/></svg>
          info@northvale.com
        </li>
        <li>
          <svg class="contact-icon" viewBox="0 0 24 24" aria-hidden="true"><circle cx="12" cy="12" r="10"/><path d="M7 8c2 0 3 1 3 2.5S8.5 13 9 15s2 2 2 4M14 4c0 2 2 2 3 3s-1 3 1 4 3 0 3 0" fill="none" stroke="#f4f4f4" stroke-width="1.6"/></svg>
          www.northvale.com
        </li>
      </ul>
    </div>
  </section>

  <section class="card card-back">
    <div class="brand">northvale</div>
  </section>
</main>
</body>
</html>
```